Corvane Business Cards

Front of business card will have logo, name, address, & telephone number. Back of card will have a list of services provided - Roads, Substation Pads, Temporary Pads, Site Pads, Land Leveling, Powerline Row Cleaning, Land Clearing, Gates, Fencing, Construction Entrances, Excavation, Trenching, Underground Utilities, Directional Boring, Pile Driving. We are a construction company that uses heavy equipment like bulldozers, motor graders/blades, dump trucks, backhoes, hydro axes, & skid loaders. We build roads, pads, & install electric utility lines & waterlines underground. This logo is new. The word "Construction" can be smaller as uploaded 2 example edited logos. We will be using this card design for many employees.
Target Market(s)
Industrial Electric Powerline, Wind Turbine, Solar Panel, & Water Utility companies.
Contact Information for Business Card
Name/Position - Dwayne Halster - Owner
Address: 4875 FM 309
Brackton, TX 79412
Phone number - (555) 482-5096

```html
<!DOCTYPE html>
<html lang="en">
<head>
<meta charset="utf-8">
<title>Corvane Construction – Business Cards</title>
<link rel="stylesheet" href="https://fonts.googleapis.com/css2?family=Marcellus&family=Poppins:wght@400;600&display=swap">
<style>
  :root {
    --backdrop: #a4a5a5;
    --card-paper: #e8e8ec;
    --maroon: #2e0b13;
    --ink: #3a3a3e;
    --paper-text: #ececee;
  }
  * { box-sizing: border-box; margin: 0; padding: 0; }
  html, body {
    width: 1105px; height: 1200px; overflow: hidden;
    background: var(--backdrop);
  }
  .canvas { position: relative; width: 1105px; height: 1200px; }
  .card {
    position: absolute; left: 182px;
    width: 744px; height: 427px;
    background: var(--card-paper);
    overflow: hidden;
  }
  .card--front { top: 119px; }
  .card--back { top: 637px; }
  .card__wave { position: absolute; inset: 0; width: 100%; height: 100%; }
  .card__wave path { fill: var(--maroon); }

  .brand {
    position: absolute; left: 74px; top: 84px;
    display: flex; align-items: center; gap: 14px;
    font-family: "Poppins", sans-serif; font-weight: 600;
    color: var(--maroon);
  }
  .brand__square { width: 22px; height: 22px; background: var(--maroon); }
  .brand__name { font-size: 52px; line-height: 1; letter-spacing: 1px; }
  .brand__line {
    position: absolute; left: 74px; top: 168px;
    font-family: "Poppins", sans-serif; font-weight: 600;
    font-size: 23px; letter-spacing: 1px; color: var(--maroon);
  }

  .person {
    position: absolute; left: 364px; width: 364px; top: 300px;
    text-align: center; color: var(--paper-text);
  }
  .person__name {
    font-family: "Marcellus", serif; font-size: 32px; letter-spacing: 1px;
    line-height: 1; white-space: nowrap;
  }
  .person__role {
    margin-top: 12px;
    display: flex; align-items: center; justify-content: center; gap: 8px;
    font-family: "Poppins", sans-serif; font-size: 14px; letter-spacing: 1px;
  }
  .person__role::before, .person__role::after {
    content: ""; width: 58px; height: 1px; background: var(--paper-text);
  }

  .services {
    position: absolute; left: 35px; top: 32px; list-style: none;
    font-family: "Poppins", sans-serif; font-size: 17px; line-height: 21px;
    color: var(--ink);
  }
  .services li { display: flex; align-items: center; gap: 7px; white-space: nowrap; }
  .services li::before {
    content: ""; width: 0; height: 0;
    border-top: 4px solid transparent; border-bottom: 4px solid transparent;
    border-left: 13px solid var(--maroon);
  }

  .contact {
    position: absolute; left: 393px; top: 305px;
    font-family: "Poppins", sans-serif; color: var(--paper-text);
    white-space: nowrap;
  }
  .contact__phone { font-size: 38px; line-height: 1.1; letter-spacing: 0.5px; }
  .contact__address { font-size: 19px; margin-top: 6px; }
</style>
</head>
<body>
<main class="canvas">
  <section class="card card--front" aria-label="Card front">
    <svg class="card__wave" viewBox="0 0 746 427" preserveAspectRatio="none" aria-hidden="true">
      <path d="M87 427 C150 395 200 375 232 358 C265 340 275 300 301 296 C340 290 375 292 398 282 C430 268 450 250 467 233 C490 210 490 185 508 178 C530 170 545 168 563 157 C590 140 600 115 619 102 C640 88 650 75 660 61 C675 40 690 25 702 19 C715 12 722 4 729 0 L746 0 L746 427 Z"/>
    </svg>
    <div class="brand">
      <span class="brand__square"></span>
      <span class="brand__name">CORVANE</span>
    </div>
    <div class="brand__line">CONSTRUCTION</div>
    <div class="person">
      <div class="person__name">DWAYNE HALSTER</div>
      <div class="person__role">OWNER</div>
    </div>
  </section>

  <section class="card card--back" aria-label="Card back">
    <svg class="card__wave" viewBox="0 0 746 427" preserveAspectRatio="none" aria-hidden="true">
      <path d="M87 427 C150 395 200 375 232 358 C265 340 275 300 301 296 C340 290 375 292 398 282 C430 268 450 250 467 233 C490 210 490 185 508 178 C530 170 545 168 563 157 C590 140 600 115 619 102 C640 88 650 75 660 61 C675 40 690 25 702 19 C715 12 722 4 729 0 L746 0 L746 427 Z"/>
    </svg>
    <ul class="services">
      <li>Roads</li>
      <li>Substation Pads</li>
      <li>Temporary Pads</li>
      <li>Site Pads</li>
      <li>Land Leveling</li>
      <li>Powerline Row Cleaning</li>
      <li>Land Clearing</li>
      <li>Gates</li>
      <li>Fencing</li>
      <li>Construction Entrances</li>
      <li>Excavation</li>
      <li>Trenching</li>
      <li>Underground Utilities</li>
      <li>Directional Boring</li>
      <li>Pile Driving</li>
    </ul>
    <div class="contact">
      <div class="contact__phone">(555) 482-5096</div>
      <div class="contact__address">4875 FM 309, Brackton, TX 79412</div>
    </div>
  </section>
</main>
</body>
</html>
```